Business Card Design

Company is a Commercial Building Company specialising in New Construction and existing refurbishments

Industry/Entity Type

Business

Contact Information for Business Card

Liam Porter
Construction Manager
E Liam@marshbuilding.com.au
M 0400 213 594
Mail 14 Tarrant Rise Kestrel Bay WA 6219

```html
<!DOCTYPE html>
<html lang="en">
<head>
<meta charset="utf-8">
<title>Marsh Building &amp; Construction – Business Card</title>
<link rel="stylesheet" href="https://fonts.googleapis.com/css2?family=Montserrat:wght@700&family=Roboto:wght@300;400&display=swap">
<style>
  :root {
    --bg: #e9e6e2;
    --card: #ffffff;
    --navy: #1f2a44;
    --ink: #1a1a1a;
    --cyan: #12b5d6;
    --orange: #f28c1e;
    --shadow: rgba(0,0,0,0.18);
  }
  * { margin: 0; padding: 0; box-sizing: border-box; }
  html, body { width: 1200px; height: 848px; overflow: hidden; }
  body {
    background: var(--bg);
    font-family: "Roboto", Arial, sans-serif;
    display: flex;
    flex-direction: column;
    align-items: center;
    justify-content: center;
    gap: 40px;
  }
  .card {
    position: relative;
    width: 600px;
    height: 367px;
    background: var(--card);
    box-shadow: 0 6px 18px var(--shadow);
    overflow: hidden;
  }
  .brand {
    display: flex;
    align-items: center;
    gap: 12px;
    color: var(--navy);
    font-family: "Montserrat", Arial, sans-serif;
    font-weight: 700;
    text-transform: uppercase;
    line-height: 1.1;
  }
  .brand-mark {
    flex: none;
    width: 34px;
    height: 34px;
    background: var(--cyan);
  }
  .front .brand {
    position: absolute;
    left: 42px;
    top: 118px;
    font-size: 21px;
  }
  .person {
    position: absolute;
    right: 52px;
    top: 46px;
    text-align: right;
    color: var(--ink);
  }
  .person-name { font-weight: 300; font-size: 27px; letter-spacing: -0.3px; }
  .person-role { font-weight: 300; font-size: 13px; margin-top: 2px; }
  .contact {
    position: absolute;
    right: 40px;
    top: 150px;
    list-style: none;
    text-align: right;
    font-weight: 300;
    font-size: 13.5px;
    color: var(--ink);
  }
  .contact li {
    display: flex;
    justify-content: flex-end;
    align-items: center;
    gap: 8px;
    height: 21px;
  }
  .contact svg { width: 12px; height: 12px; flex: none; }
  .accent-band {
    position: absolute;
    left: 0;
    bottom: 0;
    width: 600px;
    height: 56px;
    background: linear-gradient(90deg, var(--cyan), var(--orange));
  }
  .back { display: flex; align-items: center; justify-content: center; }
  .back .brand { font-size: 24px; }
  .back .brand-mark { width: 40px; height: 40px; }
</style>
</head>
<body>

<section class="card front">
  <div class="accent-band" role="img" aria-label="Decorative cyan and orange accent band along the bottom edge"></div>

  <div class="brand">
    <span class="brand-mark"></span>
    <span>Marsh Building<br>&amp; Construction</span>
  </div>

  <div class="person">
    <p class="person-name">Liam Porter</p>
    <p class="person-role">Construction Manager</p>
  </div>

  <ul class="contact">
    <li>0400 213 594
      <svg viewBox="0 0 12 12"><rect x="3" y="0.5" width="6" height="11" rx="1.2" fill="none" stroke="var(--orange)" stroke-width="1.2"/><line x1="5" y1="9.5" x2="7" y2="9.5" stroke="var(--orange)"/></svg>
    </li>
    <li>Liam@marshbuilding.com.au
      <svg viewBox="0 0 12 12"><rect x="0.5" y="2.5" width="11" height="7" fill="var(--orange)"/><path d="M0.5 2.5 L6 7 L11.5 2.5" fill="none" stroke="#fff" stroke-width="1"/></svg>
    </li>
    <li>14 Tarrant Rise Kestrel Bay WA 6219
      <svg viewBox="0 0 12 12"><path d="M6 11.5 C3 8 2 6.2 2 4.5 A4 4 0 0 1 10 4.5 C10 6.2 9 8 6 11.5 Z" fill="var(--orange)"/><circle cx="6" cy="4.5" r="1.5" fill="#fff"/></svg>
    </li>
  </ul>
</section>

<section class="card back">
  <div class="brand">
    <span class="brand-mark"></span>
    <span>Marsh Building<br>&amp; Construction</span>
  </div>
</section>

</body>
</html>
```